Website Design for The Elder Nook

Please design and code a new website.
Here are the sites I like best:
http://www.voyaglint.com/alternate/
http://www.wheelgiftbay.org
Please make it similar but look at the competitor site (below) for images and wording. This is NOT a car donation site. It's a senior lead placement site like https://www.kinhavenfinder.com. I just like this sites above as a lead generation sites.
Competitor site:
https://www.kinhavenfinder.com (use ideas / verbiage from this site)
Updates
Competitor site:
Coding
Coded - Design and coding required
Number of Pages Required
1 page
Look and feel
Each slider illustrates characteristics of the customer's brand and the style your logo design should communicate.

```html
<!DOCTYPE html>
<html lang="en">
<head>
<meta charset="utf-8">
<title>The Elder Nook — Senior Living Advisors</title>
<link href="https://fonts.googleapis.com/css2?family=Exo+2:wght@400;500&family=Montserrat:wght@400;500;600&display=swap" rel="stylesheet">
<style>
:root{
  --navy:#0f2a8c;
  --red:#e63b30;
  --ink:#222;
  --muted:#555;
  --grey-bg:#f1f2f5;
  --line:#cfd3da;
  --black:#050505;
}
*{box-sizing:border-box;margin:0;padding:0}
html,body{width:1200px;height:2904px;overflow:hidden;background:#fff}
body{font-family:"Montserrat",sans-serif;color:var(--ink)}
.canvas{position:relative;width:1200px;height:2904px;overflow:hidden}
.abs{position:absolute}
.center{left:0;width:1200px;text-align:center}
.title{font-family:"Exo 2",sans-serif;font-weight:400;font-size:29px;color:var(--navy);letter-spacing:.5px}
.title em{font-style:normal;color:var(--red)}
.rule{position:absolute;left:564px;width:72px;height:3px;background:linear-gradient(90deg,var(--navy) 0 34px,transparent 34px 38px,var(--red) 38px)}

/* header */
.brand-name{font-family:"Montserrat",sans-serif;font-weight:400;color:var(--navy);font-size:27px}
.brand-tag{font-size:11px;color:var(--red);display:flex;align-items:center;gap:10px}
.brand-tag::before,.brand-tag::after{content:"";width:22px;height:1px;background:#333}
.navbar{top:83px;left:0;width:1200px;height:35px;background:var(--navy)}
.nav a{position:absolute;top:0;height:35px;line-height:35px;color:#fff;font-size:12px;font-weight:500;text-decoration:none}
.nav a.active{background:var(--red);padding:0 17px;left:141px;width:126px}
.hero-photo{top:118px;left:0;width:1200px;height:353px;background:radial-gradient(ellipse at 45% 55%,#e9e4d8 0 18%,transparent 40%),linear-gradient(90deg,#7e9a3a,#b4c05a 30%,#d9d3b0 50%,#6f8c2c 80%,#a8b84c)}
.lead-panel{top:0;left:748px;width:282px;height:471px;background:var(--red);color:#fff}
.ribbon{top:80px;left:742px;width:294px;height:38px;background:#fff;color:#111;font-size:13px;text-align:center;line-height:38px;clip-path:polygon(0 0,100% 0,96% 50%,100% 100%,0 100%,4% 50%)}
.field{position:absolute;background:#fff;border-radius:2px;height:25px;font-size:10px;color:#555;padding-left:10px;line-height:25px}
.field.sel::after{content:"";position:absolute;right:10px;top:10px;border:4px solid transparent;border-top:5px solid #222}
.btn-navy{background:var(--navy);color:#fff;border-radius:20px;text-align:center}

/* features */
.feature{position:absolute;top:664px;width:200px;text-align:center}
.feature .ring{width:120px;height:120px;margin:0 auto;border-radius:50%;border:3px solid var(--navy);padding:3px;background:#fff}
.feature .disc{width:108px;height:108px;border-radius:50%;background:var(--red);display:flex;align-items:center;justify-content:center}
.feature p{margin-top:14px;font-size:13px;font-weight:600;line-height:18px;color:#222}

/* cost band */
.cost-band{top:908px;left:0;width:1200px;height:353px;background:linear-gradient(90deg,#3c3a2c,#6a6147 35%,#8a7e60 55%,#514c3c 80%,#2e2d26)}
.cost-band .shade{position:absolute;inset:0;background:rgba(20,20,20,.35)}

/* advisor cards */
.card{position:absolute;top:1449px;width:283px;height:108px;border:1px solid #bbb;border-radius:4px}
.card h3{position:absolute;left:71px;top:12px;font-size:14.5px;font-weight:400;line-height:20px;color:#111;width:200px}
.card p{position:absolute;left:71px;top:62px;font-size:11px;line-height:17px;color:#444}
.card svg{position:absolute;left:14px;top:14px}
.search-bar{top:1600px;left:353px;width:494px;height:34px}
.search-bar .input{position:absolute;left:0;top:0;width:250px;height:34px;border:1px solid #888;border-radius:17px 0 0 17px;font-size:13.5px;color:#888;line-height:32px;padding-left:42px}
.search-bar .go{position:absolute;left:246px;top:0;width:248px;height:34px;border-radius:0 17px 17px 0;background:var(--navy);color:#fff;font-size:16px;line-height:34px;text-align:center}

/* testimonials */
.reviews{top:1704px;left:0;width:1200px;height:425px;background:var(--grey-bg)}
.avatar{position:absolute;top:1945px;width:74px;height:74px;border-radius:10px}

/* states */
.states-box{top:2286px;left:140px;width:920px;height:385px;background:#fff;border-radius:6px;box-shadow:0 0 12px rgba(0,0,0,.12)}
.tabs{position:absolute;left:0;top:0;width:920px;height:53px;background:#f5f5f5;border-radius:6px 6px 0 0}
.tab{position:absolute;top:0;height:53px;font-size:13px;font-weight:500;line-height:17px;text-align:center;padding-top:9px;color:#222}
.tab.on{background:#fff;color:var(--red);border-radius:6px 6px 0 0;box-shadow:0 -3px 6px rgba(0,0,0,.08)}
.col{position:absolute;top:82px;list-style:none;font-size:11.5px;line-height:16.9px;color:#333}

/* footer */
.footer{top:2743px;left:0;width:1200px;height:128px;background:var(--black);color:#fff}
.footer .fnav{position:absolute;top:20px;font-size:11.5px;font-weight:500}
.contact{position:absolute;top:72px;display:flex;gap:10px;font-size:11.5px;line-height:16px}
.contact .ic{width:26px;height:26px;border:1.5px solid #fff;border-radius:50%;flex:none;display:flex;align-items:center;justify-content:center;margin-top:2px}
.copy-bar{top:2871px;left:0;width:1200px;height:33px;background:var(--red);color:#fff;font-size:11.5px}
.social{position:absolute;top:5px;width:25px;height:25px;border:1.5px solid #fff;border-radius:50%}
</style>
</head>
<body>
<div class="canvas">

  <!-- header -->
  <header>
    <div class="abs" style="left:141px;top:14px">
      <div class="brand-name">The Elder Nook</div>
      <div class="brand-tag" style="margin-top:2px">Seniorcare Nonprofit</div>
    </div>
    <nav class="abs navbar nav">
      <a class="active" href="#">Assisted Living</a>
      <a href="#" style="left:296px">Memory Care</a>
      <a href="#" style="left:432px">Nursing Homes</a>
      <a href="#" style="left:584px">More Living Options &nbsp;<svg width="9" height="6" viewBox="0 0 9 6"><path d="M0 0h9L4.5 6z" fill="#fff"/></svg></a>
    </nav>
  </header>

  <!-- hero -->
  <div class="abs hero-photo" role="img" aria-label="Photo of a smiling senior couple walking together outdoors among green trees"></div>
  <aside class="abs lead-panel">
    <svg class="abs" style="left:22px;top:38px" width="20" height="20" viewBox="0 0 24 24"><path fill="#fff" d="M6.6 10.8a15.1 15.1 0 0 0 6.6 6.6l2.2-2.2c.3-.3.7-.4 1-.2 1.1.4 2.3.6 3.6.6.6 0 1 .4 1 1V20c0 .6-.4 1-1 1A17 17 0 0 1 3 4c0-.6.4-1 1-1h3.5c.6 0 1 .4 1 1 0 1.2.2 2.4.6 3.6.1.3 0 .7-.2 1z"/></svg>
    <div class="abs" style="left:52px;top:18px;font-family:'Exo 2',sans-serif;font-size:17px;line-height:20px">Need help? Call<br><span style="font-size:21px">800-555-0147</span></div>
    <div class="abs" style="left:207px;top:21px;width:57px;height:34px;border:1px solid #fff;border-radius:2px">
      <div class="abs" style="left:11px;top:11px;width:20px;height:12px;background:#fff"></div>
      <svg class="abs" style="left:37px;top:15px" width="8" height="5" viewBox="0 0 8 5"><path d="M0 0h8L4 5z" fill="#fff"/></svg>
    </div>
    <div class="abs" style="left:0;top:140px;width:282px;text-align:center;font-size:13px;font-weight:500">Find Senior Living Near You.</div>
    <div class="field" style="left:25px;top:177px;width:106px">Firest Name</div>
    <div class="field" style="left:151px;top:177px;width:106px">Last Name</div>
    <div class="field" style="left:25px;top:214px;width:232px">Phone Number</div>
    <div class="field" style="left:25px;top:255px;width:232px">Email Address</div>
    <div class="field sel" style="left:25px;top:294px;width:106px">Select State</div>
    <div class="field sel" style="left:151px;top:294px;width:106px">select City</div>
    <div class="field" style="left:25px;top:334px;width:232px">Zip Code</div>
    <div class="abs btn-navy" style="left:25px;top:380px;width:232px;height:35px;line-height:35px;font-size:15.5px">Start Your Search</div>
  </aside>
  <div class="abs ribbon">Talk to a local advisor for FREE</div>

  <!-- support -->
  <section>
    <h2 class="abs center title" style="top:535px">The support you need to make the <em>RIGHT CHOICE</em></h2>
    <div class="rule" style="top:583px"></div>
    <p class="abs center" style="top:604px;font-size:11.5px;line-height:18px">Kinhaven Finder has already helped thousands of families find peace of<br>mind. Here’s what’s included with our free service:</p>

    <div class="feature" style="left:101px"><div class="ring"><div class="disc">
      <svg width="52" height="56" viewBox="0 0 52 56"><circle cx="26" cy="15" r="13" fill="#fff"/><path d="M4 56c0-18 8-26 22-26s22 8 22 26z" fill="#fff"/></svg></div></div>
      <p>Dedicated local<br>advisor</p></div>
    <div class="feature" style="left:301px"><div class="ring"><div class="disc">
      <svg width="56" height="50" viewBox="0 0 56 50"><path d="M28 2 2 26h8v22h14V34h8v14h14V26h8z" fill="#fff"/></svg></div></div>
      <p>Hand-picked list of<br>communities to match<br>your needs</p></div>
    <div class="feature" style="left:500px"><div class="ring"><div class="disc">
      <svg width="36" height="60" viewBox="0 0 36 60"><path d="M18 2v56M30 14c-3-4-7-5-12-5-6 0-11 3-11 9 0 13 23 7 23 21 0 6-5 10-12 10-6 0-10-2-13-6" fill="none" stroke="#fff" stroke-width="6"/></svg></div></div>
      <p>Full details and<br>pricing</p></div>
    <div class="feature" style="left:700px"><div class="ring"><div class="disc">
      <svg width="50" height="50" viewBox="0 0 50 50"><rect x="3" y="7" width="44" height="40" rx="3" fill="#fff"/><rect x="11" y="1" width="5" height="10" fill="#fff"/><rect x="34" y="1" width="5" height="10" fill="#fff"/><g fill="#e63b30"><rect x="7" y="17" width="7" height="6"/><rect x="17" y="17" width="7" height="6"/><rect x="27" y="17" width="7" height="6"/><rect x="37" y="17" width="6" height="6"/><rect x="7" y="26" width="7" height="6"/><rect x="17" y="26" width="7" height="6"/><rect x="27" y="26" width="7" height="6"/><rect x="37" y="26" width="6" height="6"/><rect x="7" y="35" width="7" height="6"/><rect x="17" y="35" width="7" height="6"/><rect x="27" y="35" width="7" height="6"/><rect x="37" y="35" width="6" height="6"/></g></svg></div></div>
      <p>Help scheduling<br>tours</p></div>
    <div class="feature" style="left:899px"><div class="ring"><div class="disc">
      <svg width="58" height="46" viewBox="0 0 58 46"><rect x="18" y="2" width="38" height="32" rx="2" fill="#fff"/><path d="M16 12H8L2 24v12h14z" fill="#fff"/><circle cx="14" cy="38" r="7" fill="#fff" stroke="#e63b30" stroke-width="3"/><circle cx="44" cy="38" r="7" fill="#fff" stroke="#e63b30" stroke-width="3"/></svg></div></div>
      <p>Move in support</p></div>
  </section>

  <!-- no cost band -->
  <section class="abs cost-band" role="img" aria-label="Photo of a caregiver laughing with an elderly woman seated outdoors">
    <div class="shade"></div>
  </section>
  <div class="abs center title" style="top:972px;color:#fff;font-size:27px">There’s no <em>cost</em> to you.</div>
  <div class="rule" style="top:1020px;background:linear-gradient(90deg,#fff 0 34px,transparent 34px 38px,var(--red) 38px)"></div>
  <p class="abs center" style="top:1041px;color:#eee;font-size:13px;line-height:19px">We work with over 20,000 senior living communities.<br>Our community partners pay us for placement<br>services.</p>
  <div class="abs center" style="top:1110px;color:#fff;font-family:'Exo 2',sans-serif;font-size:21px">
    <svg width="18" height="18" viewBox="0 0 24 24" style="vertical-align:-2px;margin-right:6px"><path fill="#fff" d="M6.6 10.8a15.1 15.1 0 0 0 6.6 6.6l2.2-2.2c.3-.3.7-.4 1-.2 1.1.4 2.3.6 3.6.6.6 0 1 .4 1 1V20c0 .6-.4 1-1 1A17 17 0 0 1 3 4c0-.6.4-1 1-1h3.5c.6 0 1 .4 1 1 0 1.2.2 2.4.6 3.6.1.3 0 .7-.2 1z"/></svg>Call800-555-0147</div>
  <div class="abs btn-navy" style="left:509px;top:1155px;width:181px;height:34px;line-height:34px;font-size:16px;font-family:'Exo 2',sans-serif">Contact Now &nbsp;
    <svg width="18" height="16" viewBox="0 0 18 16" style="vertical-align:-2px"><path d="M0 7 18 0 14 16 9 11 15 3 7 10z" fill="#fff"/></svg></div>

  <!-- advisor -->
  <section>
    <h2 class="abs center title" style="top:1324px">Your <em>LOCAL ADVISOR</em> informs. You decide.</h2>
    <div class="rule" style="top:1372px"></div>
    <p class="abs center" style="top:1395px;font-size:11px">Over 400 senior advisors across the U.S. and Canada are ready to help your family with:</p>
    <div class="card" style="left:141px">
      <svg width="30" height="58" viewBox="0 0 30 58"><circle cx="14" cy="12" r="11" fill="none" stroke="#e63b30" stroke-width="1.5"/><circle cx="11" cy="10" r="3" fill="none" stroke="#e63b30" stroke-width="1.5"/><path d="M14 23v34" stroke="#e63b30" stroke-width="1.5"/></svg>
      <h3>Insider’s tips for the area near you</h3><p>Lorem ipsum dolor sit amet,<br>consectetur adipiscing elit.</p></div>
    <div class="card" style="left:458px">
      <svg width="46" height="42" viewBox="0 0 46 42"><path d="M23 40S2 26 2 13C2 6 7 2 12 2c5 0 9 3 11 7 2-4 6-7 11-7 5 0 10 4 10 11 0 13-21 27-21 27z" fill="none" stroke="#e63b30" stroke-width="1.5"/></svg>
      <h3>Advice tailored to your unique situation</h3><p>Lorem ipsum dolor sit amet,<br>consectetur adipiscing elit.</p></div>
    <div class="card" style="left:775px">
      <svg width="44" height="44" viewBox="0 0 44 44"><circle cx="22" cy="22" r="20" fill="none" stroke="#e63b30" stroke-width="1.5"/><path d="M22 8v14H10" fill="none" stroke="#e63b30" stroke-width="1.5"/></svg>
      <h3>Time saving know-how and resources</h3><p>Lorem ipsum dolor sit amet,<br>consectetur adipiscing elit.</p></div>
    <div class="abs search-bar"><div class="input">Enter city or postal code</div><div class="go">Find An Advisor Near You</div></div>
  </section>

  <!-- reviews -->
  <section class="abs reviews"></section>
  <h2 class="abs center title" style="top:1769px"><em>97%</em> of our customers recommend our service</h2>
  <div class="rule" style="top:1816px"></div>
  <p class="abs center" style="top:1849px;font-size:13px;font-style:italic;color:#444">“You were a great help. We really appreciate you &amp; Kinhaven Finder!”</p>
  <p class="abs center" style="top:1883px;font-size:12px;font-weight:600;color:#333">DALE R</p>
  <p class="abs center" style="top:1909px;font-size:9.5px;color:#555">Looking for Senior Living for his wife in Denver, CO</p>
  <div class="avatar" style="left:454px;background:linear-gradient(#eee,#cfcfcf);opacity:.75" role="img" aria-label="Portrait of a senior man"></div>
  <div class="avatar" style="left:563px;border:4px solid var(--red);background:linear-gradient(#7fb3d6,#d9c3a6)" role="img" aria-label="Portrait of a senior couple at the beach"></div>
  <div class="avatar" style="left:672px;background:linear-gradient(#f4f4f4,#c9d8d4);opacity:.75" role="img" aria-label="Portrait of a senior woman"></div>
  <div class="abs" style="left:581px;top:2050px;width:8px;height:8px;border-radius:50%;background:#d0021b"></div>
  <div class="abs" style="left:596px;top:2050px;width:8px;height:8px;border-radius:50%;background:#ccc"></div>
  <div class="abs" style="left:610px;top:2050px;width:8px;height:8px;border-radius:50%;background:#ccc"></div>

  <!-- states -->
  <section>
    <h2 class="abs center title" style="top:2193px">Senior Living by <em>State</em></h2>
    <div class="rule" style="top:2241px"></div>
    <div class="abs states-box">
      <div class="tabs">
        <div class="tab" style="left:10px;width:94px">Memory<br>Care</div>
        <div class="tab on" style="left:105px;width:153px">Assisted<br>Living</div>
        <div class="tab" style="left:262px;width:140px">Independent<br>Living</div>
        <div class="tab" style="left:416px;width:90px">Nursing<br>Home</div>
        <div class="tab" style="left:532px;width:90px">Care<br>Homes</div>
      </div>
      <ul class="col" style="left:24px"><li>Alabama</li><li>Arizona</li><li>Arkansas</li><li>California</li><li>Colorado</li><li>Connecticut</li><li>Delaware</li><li>District of Columbia</li><li>Florida</li><li>Georgia</li><li>Hawaii</li><li>Idaho</li><li>Illinois</li><li>Indiana</li><li>Iowa</li><li>Kansas</li><li>Kentucky</li></ul>
      <ul class="col" style="left:324px"><li>Louisiana</li><li>Maine</li><li>Maryland</li><li>Massachusetts</li><li>Michigan</li><li>Minnesota</li><li>Mississippi</li><li>Missouri</li><li>Montana</li><li>Nebraska</li><li>Nevada</li><li>New Hampshire</li><li>New Jersey</li><li>New Mexico</li><li>New York</li><li>North Carolina</li><li>North Dakota</li></ul>
      <ul class="col" style="left:649px"><li>Ohio</li><li>Oklahoma</li><li>Oregon</li><li>Pennsylvania</li><li>Rhode Island</li><li>South Carolina</li><li>South Dakota</li><li>Tennessee</li><li>Texas</li><li>Utah</li><li>Vermont</li><li>Virginia</li><li>Washington</li><li>West Virginia</li><li>Wisconsin</li><li>Wyoming</li></ul>
    </div>
  </section>

  <!-- footer -->
  <footer class="abs footer">
    <div class="fnav" style="left:142px">Assisted Living</div>
    <div class="fnav" style="left:279px">Memory Care</div>
    <div class="fnav" style="left:415px">Nursing Homes</div>
    <div class="fnav" style="left:567px">More Living Options &nbsp;<svg width="9" height="6" viewBox="0 0 9 6"><path d="M0 0h9L4.5 6z" fill="#fff"/></svg></div>
    <div class="abs" style="left:142px;top:54px;width:670px;height:1px;background:#333"></div>
    <div class="contact" style="left:182px"><span class="ic"><svg width="10" height="13" viewBox="0 0 10 13"><path d="M5 13S0 7 0 5a5 5 0 0 1 10 0c0 2-5 8-5 8z" fill="#2a4fd0"/></svg></span><div><b>Address</b><br>124 Maple Row, Suite 902, Springdale,<br>NY 10016</div></div>
    <div class="contact" style="left:470px"><span class="ic"><svg width="11" height="11" viewBox="0 0 24 24"><path fill="#2a4fd0" d="M6.6 10.8a15.1 15.1 0 0 0 6.6 6.6l2.2-2.2c.3-.3.7-.4 1-.2 1.1.4 2.3.6 3.6.6.6 0 1 .4 1 1V20c0 .6-.4 1-1 1A17 17 0 0 1 3 4c0-.6.4-1 1-1h3.5c.6 0 1 .4 1 1 0 1.2.2 2.4.6 3.6.1.3 0 .7-.2 1z"/></svg></span><div><b>Call Us :</b><br>800-555-0147</div></div>
    <div class="contact" style="left:616px"><span class="ic"><svg width="12" height="9" viewBox="0 0 12 9"><rect width="12" height="9" rx="1" fill="#2a4fd0"/></svg></span><div><b>Email Us :</b><br>info@eldernook.example</div></div>
    <div class="abs" style="left:870px;top:34px;width:189px;text-align:right">
      <div class="brand-name" style="color:#fff;font-size:25px">The Elder Nook</div>
      <div class="brand-tag" style="color:#fff;justify-content:flex-end;margin-top:2px">Seniorcare Nonprofit</div>
    </div>
  </footer>
  <div class="abs copy-bar">
    <div class="abs" style="left:141px;top:10px">Copyright 2019 The Elder Nook Seniorcare Nonprofit . All Rights Reserved.</div>
    <div class="social" style="left:962px"></div>
    <div class="social" style="left:998px"></div>
    <div class="social" style="left:1033px"></div>
  </div>

</div>
</body>
</html>
```